VELMOR Website Design

We need a website designed for our company VELMOR. We are a luxury lifestyle club that will provide benefits and services for our members. The site should be clean & sleek, preferably using black and white (or darker colors). (example sites: stravenhall.example, plinth.example)

Here is a link of a sample page I did using wix. (https://dunmere7.sitehostly.example/mysite) This can be used to get a general idea.

Target Market(s)

Upper Middle Class in the United States

Number of Pages Required

5+ page

Font styles to use
Sans Serif
Other font styles liked:
• Arial (or other similar fonts)

Requirements
Must have
• A clean design that is eye-catching and speaks to our company.
Nice to have
• Ideas for copy.

```html
<!DOCTYPE html>
<html lang="en">
<head>
<meta charset="utf-8">
<title>VELMOR — Member Speaks</title>
<link rel="stylesheet" href="https://fonts.googleapis.com/css2?family=Montserrat:wght@600;700&family=Roboto:wght@400&display=swap">
<style>
  :root {
    --page-bg: #f8f8f8;
    --card-bg: #ffffff;
    --heading: #3a3a3a;
    --body-text: #737373;
    --accent: #17b4ea;
    --arrow-muted: #c9c9c9;
    --white: #ffffff;
  }
  * { box-sizing: border-box; margin: 0; padding: 0; }
  html, body { width: 1200px; height: 870px; overflow: hidden; }
  body { background: var(--page-bg); font-family: "Roboto", Arial, sans-serif; position: relative; }

  .testimonials { position: absolute; left: 0; top: 0; width: 1200px; height: 473px; background: var(--page-bg); }
  .section-title {
    position: absolute; top: 54px; width: 100%; text-align: center;
    font-family: "Montserrat", Arial, sans-serif; font-weight: 700; font-size: 34px;
    color: var(--heading); letter-spacing: 0.5px;
  }
  .slider-nav { position: absolute; top: 122px; left: 560px; display: flex; gap: 10px; }
  .slider-btn { width: 35px; height: 35px; border-radius: 50%; display: flex; align-items: center; justify-content: center; }
  .slider-btn--prev { border: 1.5px solid var(--arrow-muted); }
  .slider-btn--next { background: var(--accent); }

  .card {
    position: absolute; top: 191px; width: 290px; height: 213px; background: var(--card-bg);
    box-shadow: 0 6px 18px rgba(0,0,0,0.06); text-align: center;
  }
  .card--1 { left: 132px; } .card--2 { left: 455px; } .card--3 { left: 778px; }
  .avatar { width: 54px; height: 54px; border-radius: 50%; margin: 23px auto 0; }
  .avatar--john { background: radial-gradient(circle at 50% 40%, #b8a89a, #6a6560); }
  .avatar--peter { background: radial-gradient(circle at 50% 40%, #c9b39e, #3d3530); }
  .avatar--claire { background: radial-gradient(circle at 50% 40%, #c49a82, #4a3a30); }
  .member-name {
    margin-top: 13px; font-family: "Montserrat", Arial, sans-serif; font-weight: 600;
    font-size: 14px; color: var(--heading);
  }
  .quote { margin: 7px 22px 0; font-size: 13px; line-height: 21px; color: var(--body-text); }

  .experience { position: absolute; left: 0; top: 473px; width: 497px; height: 397px;
    background: linear-gradient(180deg, #2aa9e6 0%, #28a6df 60%, #1f8fc4 100%); }
  .play-btn { position: absolute; left: 399px; top: 236px; }
  .experience-kicker { position: absolute; right: 36px; top: 306px; font-family: "Montserrat", Arial, sans-serif;
    font-weight: 700; font-size: 16px; color: var(--white); letter-spacing: 0.3px; }
  .experience-title { position: absolute; right: 36px; top: 326px; font-family: "Montserrat", Arial, sans-serif;
    font-weight: 700; font-size: 33px; color: var(--white); white-space: nowrap; }

  .gallery { position: absolute; left: 497px; top: 473px; width: 703px; height: 397px;
    display: grid; grid-template-columns: 234px 235px 234px; grid-template-rows: 198px 199px; }
  .tile--singer { background: linear-gradient(135deg, #c21fd6 0%, #6a1a6e 45%, #2a0c1e 100%); }
  .tile--mixer { background: linear-gradient(160deg, #05060d 0%, #151a4a 50%, #3a4de0 100%); }
  .tile--cocktail { background: linear-gradient(160deg, #c46a48 0%, #8a5040 45%, #3a2a28 100%); }
  .tile--bar { background: linear-gradient(160deg, #1a1a2a 0%, #a06a3a 50%, #e89a2a 100%); }
  .tile--dancer { background: radial-gradient(circle at 60% 30%, #e04ae8 0%, #8a1fc0 45%, #2a0c3a 100%); }
  .tile--bottles { background: radial-gradient(circle at 50% 55%, #3ac6c0 0%, #3a2a7a 40%, #151822 75%); }
</style>
</head>
<body>
  <section class="testimonials">
    <h2 class="section-title">MEMBER SPEAKS</h2>
    <div class="slider-nav">
      <div class="slider-btn slider-btn--prev">
        <svg width="16" height="16" viewBox="0 0 16 16"><path d="M13 8H3M7 4L3 8l4 4" fill="none" stroke="#c9c9c9" stroke-width="1.6" stroke-linecap="round" stroke-linejoin="round"/></svg>
      </div>
      <div class="slider-btn slider-btn--next">
        <svg width="16" height="16" viewBox="0 0 16 16"><path d="M3 8h10M9 4l4 4-4 4" fill="none" stroke="#fff" stroke-width="2" stroke-linecap="round" stroke-linejoin="round"/></svg>
      </div>
    </div>

    <article class="card card--1">
      <div class="avatar avatar--john" role="img" aria-label="Portrait of John Smith"></div>
      <h3 class="member-name">John Smith</h3>
      <p class="quote">Phasellus tellus risus, tincidunt eu scelerisque a, blandit sed metus. Aliquam ut tristique mi. Fusce vitae dignissim enim. Nam tincidunt dictum libero sed.</p>
    </article>
    <article class="card card--2">
      <div class="avatar avatar--peter" role="img" aria-label="Portrait of Peter Hens"></div>
      <h3 class="member-name">Peter Hens</h3>
      <p class="quote">Phasellus tellus risus, tincidunt eu scelerisque a, blandit sed metus. Aliquam ut tristique mi. Fusce vitae dignissim enim. Nam tincidunt dictum libero sed.</p>
    </article>
    <article class="card card--3">
      <div class="avatar avatar--claire" role="img" aria-label="Portrait of Claire Pat"></div>
      <h3 class="member-name">Claire Pat</h3>
      <p class="quote">Phasellus tellus risus, tincidunt eu scelerisque a, blandit sed metus. Aliquam ut tristique mi. Fusce vitae dignissim enim. Nam tincidunt dictum libero sed.</p>
    </article>
  </section>

  <section class="experience" role="img" aria-label="Crowd with raised hands at a concert under blue light">
    <svg class="play-btn" width="58" height="58" viewBox="0 0 58 58">
      <circle cx="29" cy="29" r="27" fill="none" stroke="#fff" stroke-width="2.5"/>
      <path d="M23 18L40 29L23 40Z" fill="#fff"/>
    </svg>
    <div class="experience-kicker">EXPERIENCE</div>
    <div class="experience-title">WITH VELMOR</div>
  </section>

  <section class="gallery">
    <div class="tile--singer" role="img" aria-label="Woman in pink stage light at a club"></div>
    <div class="tile--mixer" role="img" aria-label="Illuminated DJ controller pads"></div>
    <div class="tile--cocktail" role="img" aria-label="Mojito cocktail on a bar counter"></div>
    <div class="tile--bar" role="img" aria-label="Guests standing at a lit bar"></div>
    <div class="tile--dancer" role="img" aria-label="Dancer with raised arms under purple lights"></div>
    <div class="tile--bottles" role="img" aria-label="Three glowing glass bottles"></div>
  </section>
</body>
</html>
```